Building company buisness cards

We are looking for a sharp modern new look for our business cards.
We are a New Zealand based company that specialises in house and land packages.
We have attached a photo of the current logo and would like to see if it can be improved somehow if needed.
We are open to any colours but we have chosen green at this stage.
Feel free to change the font and make the logo smarter looking.
Play with the colours and see what looks best.

We want a card that looks so good know one will want to throw it away!

Target Market(s)

Home buyers

Industry/Entity Type

Building

Contact Information for Business Card

Derek Tolvane
0217394062
dtolvane@quillmarkhomesteads.co.nz
quillmarkhomesteads.co.nz

Font styles to use
Serif
Sans Serif

Colors

Designer to choose colors to be used in the design.

Requirements
Must have
• Logo and company name on one side, details on the other side
Nice to have
• Color codes for the original green are HEX #4a8028, RGB(74,128,40), CMYK(42,0,69,50)
• Round corners, Raised and/or spot UV

```html
<!DOCTYPE html>
<html lang="en">
<head>
<meta charset="utf-8">
<title>Quillmark Homesteads – Business Cards</title>
<link rel="stylesheet" href="https://fonts.googleapis.com/css2?family=Open+Sans:wght@400;700;800&display=swap">
<style>
  :root {
    --brand-green: #4a8028;
    --brand-green-bright: #4f9a22;
    --rule-grey: #b9b9b9;
    --band-grey: #cfcfcf;
    --ink: #4a4a4a;
    --card: #ffffff;
    --backdrop: #e9e6e3;
  }
  html, body {
    margin: 0;
    width: 1200px;
    height: 997px;
    overflow: hidden;
    background: var(--backdrop);
    font-family: "Open Sans", Arial, sans-serif;
  }
  .sheet {
    position: relative;
    width: 1200px;
    height: 997px;
  }
  .card {
    position: absolute;
    top: 344px;
    width: 540px;
    height: 309px;
    background: var(--card);
    border-radius: 10px;
    box-shadow: 0 2px 10px rgba(0,0,0,0.08);
    overflow: hidden;
  }
  .card--details { left: 40px; }
  .card--front { left: 620px; }

  .wordmark {
    color: var(--brand-green);
    font-weight: 800;
    letter-spacing: -0.5px;
    line-height: 1;
    display: flex;
    align-items: center;
    gap: 10px;
  }
  .wordmark__dot {
    width: 14px;
    height: 14px;
    background: var(--brand-green);
    border-radius: 50%;
    flex: none;
  }

  .card--details .wordmark {
    position: absolute;
    left: 34px;
    top: 62px;
    font-size: 28px;
  }
  .holder {
    position: absolute;
    right: 34px;
    top: 84px;
    margin: 0;
    font-size: 13px;
    font-weight: 700;
    color: var(--brand-green);
    text-transform: uppercase;
    letter-spacing: 0.3px;
  }
  .holder-rule {
    position: absolute;
    left: 250px;
    right: 34px;
    top: 108px;
    height: 1px;
    background: var(--rule-grey);
  }
  .swoosh {
    position: absolute;
    left: 0;
    top: 150px;
    width: 540px;
    height: 70px;
  }
  .contacts {
    position: absolute;
    left: 34px;
    top: 226px;
    margin: 0;
    padding: 0;
    list-style: none;
    font-size: 13px;
    color: var(--ink);
    line-height: 20px;
  }
  .contacts li {
    display: flex;
    align-items: center;
    gap: 7px;
  }
  .contacts svg {
    width: 11px;
    height: 11px;
    fill: var(--brand-green);
    flex: none;
  }

  .card--front .wordmark {
    position: absolute;
    left: 0;
    right: 0;
    top: 118px;
    justify-content: center;
    font-size: 40px;
  }
  .front-rule {
    position: absolute;
    left: 240px;
    width: 60px;
    top: 186px;
    height: 1px;
    background: var(--rule-grey);
  }
</style>
</head>
<body>
<main class="sheet">

  <section class="card card--details" aria-label="Business card, details side">
    <div class="wordmark"><span class="wordmark__dot"></span>quillmark homesteads.</div>
    <p class="holder">Derek Tolvane</p>
    <div class="holder-rule"></div>

    <svg class="swoosh" viewBox="0 0 540 70" preserveAspectRatio="none" aria-hidden="true">
      <path d="M0 52 L400 52 C412 52 414 30 440 28 L540 20 L540 60 L0 60 Z" fill="var(--band-grey)"/>
      <path d="M0 55 L405 55 C420 55 420 38 448 35 L540 28 L540 55 L0 58 Z" fill="var(--band-grey)" opacity="0.6"/>
      <path d="M400 50 C410 20 425 14 460 12 L540 8 L540 28 L440 31 C418 33 412 44 404 50 Z" fill="var(--brand-green-bright)"/>
      <line x1="0" y1="62" x2="540" y2="62" stroke="var(--brand-green-bright)" stroke-width="2"/>
      <line x1="0" y1="46" x2="400" y2="46" stroke="var(--rule-grey)" stroke-width="1"/>
    </svg>

    <ul class="contacts">
      <li>
        <svg viewBox="0 0 24 24" aria-hidden="true"><path d="M6.6 10.8a15 15 0 0 0 6.6 6.6l2.2-2.2a1 1 0 0 1 1-.25 11.4 11.4 0 0 0 3.6.57 1 1 0 0 1 1 1V20a1 1 0 0 1-1 1A17 17 0 0 1 3 4a1 1 0 0 1 1-1h3.5a1 1 0 0 1 1 1c0 1.25.2 2.45.57 3.57a1 1 0 0 1-.25 1z"/></svg>
        0217394062
      </li>
      <li>
        <svg viewBox="0 0 24 24" aria-hidden="true"><path d="M2 5h20v14H2z M2 5l10 8 10-8" stroke="#fff" stroke-width="1.5"/></svg>
        dtolvane@quillmarkhomesteads.co.nz
      </li>
      <li>
        <svg viewBox="0 0 24 24" aria-hidden="true"><circle cx="12" cy="12" r="10"/><path d="M2 12h20M12 2c3 3 3 17 0 20M12 2c-3 3-3 17 0 20" stroke="#fff" stroke-width="1.3" fill="none"/></svg>
        www.quillmarkhomesteads.co.nz
      </li>
    </ul>
  </section>

  <section class="card card--front" aria-label="Business card, logo side">
    <div class="wordmark"><span class="wordmark__dot"></span>quillmark homesteads.</div>
    <div class="front-rule"></div>
  </section>

</main>
</body>
</html>
```